Shop Window Desgin

I have a big glass window (office), 280cm wide by 302cm high and I want designing an advert for our property management business.

Our main colours are in the proeprty management logo attached. I have also uploaded a photo of the shop front (left window), please take into consideration the door.

I want the following text items placed:

PROPERTY MANAGEMENT
HOLIDAY RENTALS
KEYHOLDING
MARKETING & RESERVATIONS
GARDEN & POOL MAINTENACE
CLEANING & LAUNDRY

```html
<!DOCTYPE html>
<html lang="en">
<head>
<meta charset="utf-8">
<title>Pinnacle Property Management – Shop Window</title>
<link href="https://fonts.googleapis.com/css2?family=Poppins:wght@600&family=Roboto+Condensed:ital,wght@1,700&display=swap" rel="stylesheet">
<style>
  :root {
    --orange: #e8832a;
    --orange-dark: #c9661a;
    --grey: #7b7b7b;
    --grey-text: #5e5e5e;
    --ring: #d9d9d9;
    --page: #2e2e2e;
    --white: #ffffff;
    --photo-a: #dfe6ee;
    --photo-b: #8fa3bd;
    --photo-c: #2c3c5e;
    --city-a: #fafafa;
    --city-b: #e4e4e4;
    --badge-purple: #5b4a78;
    --badge-blue: #1f86c8;
  }
  * { margin: 0; padding: 0; box-sizing: border-box; }
  html, body { width: 1200px; height: 1200px; overflow: hidden; background: var(--page); }
  .window-poster {
    position: absolute; left: 69px; top: 28px;
    width: 1062px; height: 1144px; overflow: hidden; background: var(--white);
  }
  .poster-shapes { position: absolute; inset: 0; width: 100%; height: 100%; }
  .brand {
    position: absolute; left: 52px; top: 58px; width: 460px;
    font-family: "Poppins", sans-serif; font-weight: 600; color: var(--grey-text);
    font-size: 44px; line-height: 1.12;
  }
  .services { position: absolute; left: 0; top: 768px; width: 100%; height: 210px; }
  .service { position: absolute; width: 170px; margin-left: -85px; text-align: center; }
  .service-icon {
    width: 144px; height: 144px; margin: 0 auto; border-radius: 50%;
    background: var(--orange); border: 5px solid var(--ring);
    box-shadow: inset 0 0 0 3px var(--orange-dark);
    display: flex; align-items: center; justify-content: center;
  }
  .service-icon svg { width: 70px; height: 70px; fill: none; stroke: var(--white); stroke-width: 3; stroke-linecap: round; stroke-linejoin: round; }
  .service-label {
    margin-top: 10px; font-family: "Roboto Condensed", sans-serif; font-style: italic; font-weight: 700;
    font-size: 21px; line-height: 1.05; text-transform: uppercase;
  }
  .service-label .lead { color: var(--orange); display: block; }
  .service-label .rest { color: var(--grey-text); display: block; }
  .partners { position: absolute; left: 365px; top: 1012px; display: flex; align-items: center; gap: 34px; }
  .partner-association { width: 200px; height: 56px; border-radius: 6px; background: var(--badge-purple); opacity: .85; }
  .partner-certificate { width: 94px; height: 84px; border-radius: 50%; background: var(--badge-blue); border: 4px solid var(--white); box-shadow: 0 0 0 2px var(--badge-blue); }
</style>
</head>
<body>
<main class="window-poster">
  <svg class="poster-shapes" viewBox="0 0 708 763" preserveAspectRatio="none">
    <defs>
      <linearGradient id="cityTone" x1="0" y1="0" x2="0" y2="1">
        <stop offset="0" stop-color="var(--city-a)"/>
        <stop offset="1" stop-color="var(--city-b)"/>
      </linearGradient>
      <linearGradient id="photoTone" x1="0" y1="0" x2="1" y2="0.4">
        <stop offset="0" stop-color="var(--photo-a)"/>
        <stop offset="0.45" stop-color="var(--photo-b)"/>
        <stop offset="0.75" stop-color="var(--photo-c)"/>
        <stop offset="1" stop-color="var(--photo-b)"/>
      </linearGradient>
    </defs>
    <rect class="city-backdrop" x="0" y="300" width="708" height="463" fill="url(#cityTone)" role="img" aria-label="Faint grey city skyline of tall buildings"/>
    <polygon class="hero-photo" points="0,0 708,0 708,118 220,495 0,360" fill="url(#photoTone)" role="img" aria-label="Businessman in a suit holding a glowing blue house outline in his open palm"/>
    <polygon class="grey-wedge" points="0,374 100,440 0,512" fill="var(--grey)"/>
    <polygon class="orange-wedge" points="708,133 416,370 708,552" fill="var(--orange)"/>
    <rect class="footer-stripe" x="0" y="744" width="708" height="12" fill="var(--orange)"/>
  </svg>

  <header class="brand">Pinnacle<br>Property Management</header>

  <section class="services">
    <div class="service" style="left:135px">
      <div class="service-icon"><svg viewBox="0 0 48 48"><rect x="16" y="6" width="16" height="22"/><path d="M20 11h2M26 11h2M20 16h2M26 16h2M20 21h2M26 21h2"/><path d="M6 34c6-4 12-4 18 0h10c2 0 2 3 0 3H22M6 42h24l12-8"/></svg></div>
      <div class="service-label"><span class="lead">Property</span><span class="rest">Management</span></div>
    </div>
    <div class="service" style="left:292px">
      <div class="service-icon"><svg viewBox="0 0 48 48"><path d="M5 24 24 8l19 16"/><path d="M10 20v20h28V20"/><rect x="20" y="28" width="8" height="12"/><rect x="22" y="16" width="20" height="9"/></svg></div>
      <div class="service-label"><span class="lead">Holiday</span><span class="rest">Rentals</span></div>
    </div>
    <div class="service" style="left:450px">
      <div class="service-icon"><svg viewBox="0 0 48 48"><circle cx="20" cy="36" r="6"/><path d="M22 30 30 12M30 12l6-4M32 16l4 2"/><path d="M16 8l6 12"/></svg></div>
      <div class="service-label"><span class="lead">Keyholding</span></div>
    </div>
    <div class="service" style="left:613px">
      <div class="service-icon"><svg viewBox="0 0 48 48"><path d="M8 20h8l16-9v26l-16-9H8z"/><path d="M12 28l3 10h5l-3-10"/><path d="M37 18l5-3M38 24h6M37 30l5 3"/></svg></div>
      <div class="service-label"><span class="lead">Marketing</span><span class="rest">&amp; Reservations</span></div>
    </div>
    <div class="service" style="left:771px">
      <div class="service-icon"><svg viewBox="0 0 48 48"><rect x="6" y="16" width="26" height="24"/><path d="M10 26c3-2 5 2 8 0s5 2 8 0M10 33c3-2 5 2 8 0s5 2 8 0"/><path d="M36 10a5 5 0 0 0 4 8v20"/></svg></div>
      <div class="service-label"><span class="lead">Garden &amp; Pool</span><span class="rest">Maintenace</span></div>
    </div>
    <div class="service" style="left:928px">
      <div class="service-icon"><svg viewBox="0 0 48 48"><rect x="9" y="6" width="30" height="36" rx="2"/><path d="M9 14h30"/><circle cx="24" cy="28" r="8"/><path d="M30 10h2M34 10h2"/></svg></div>
      <div class="service-label"><span class="lead">Cleaning</span><span class="rest">&amp; Laundry</span></div>
    </div>
  </section>

  <footer class="partners">
    <div class="partner-association"></div>
    <div class="partner-certificate"></div>
  </footer>
</main>
</body>
</html>
```